Business card for a Exhibition booth fabrication company

Hi. My company would like to change our corporate name card. We are an events and Exhibition stand builder company. We would like our corporate name card to resonate what we do. I need someone to create something unique that relates to the industry that I am in. The graphic designer should be creative to incorporate the elements of my industry and try to blend in well in the design of the card. Our aim is to ensure that we are unique and our card can look different from our competitors.
Updates

Target Market(s)

Marketing and events manager from all companies

Contact Information for Business Card

The business card should have the following details:
Name
Job Title
Email
Website

Colors

Designer to choose colors to be used in the design.

Requirements
Must have
• The card must be look something that is relevant to the service that I am providing. My website is: www.velmora-buildworks.com
• You can see my website to get more information on what service that I am doing
Nice to have
• On the back of my card, I would like to have a globe image with the incorporation of my company logo. This is to indicate that my services can be done in any part of the world.

```html
<!DOCTYPE html>
<html lang="en">
<head>
<meta charset="utf-8">
<title>Velmora Buildworks – Business Card</title>
<link href="https://fonts.googleapis.com/css2?family=Oswald:wght@400;500&family=Didact+Gothic&family=Montserrat:wght@500&display=swap" rel="stylesheet">
<style>
  :root {
    --bg: #3a3b3d;
    --red: #d0202a;
    --red-dark: #a3141c;
    --map-tint: rgba(255, 255, 255, 0.13);
    --black: #0c0c0d;
    --black-soft: #1c1c1e;
    --grey-text: #5b5c5f;
    --contact-text: #8e8f92;
    --white: #ffffff;
  }
  * { margin: 0; padding: 0; box-sizing: border-box; }
  html, body { width: 1200px; height: 1000px; overflow: hidden; }
  body {
    background: var(--bg);
    position: relative;
    font-family: "Didact Gothic", sans-serif;
  }
  .card {
    position: absolute;
    width: 620px;
    height: 360px;
    border-radius: 26px;
    overflow: hidden;
  }

  /* Front */
  .card-front {
    left: 500px;
    top: 60px;
    background: linear-gradient(135deg, var(--red) 0%, var(--red) 55%, var(--red-dark) 100%);
  }
  .world-map-area {
    position: absolute;
    left: 40px;
    top: 18px;
    width: 560px;
    height: 320px;
    border-radius: 40% 45% 35% 40%;
    background:
      radial-gradient(ellipse 22% 30% at 22% 30%, var(--map-tint) 0%, rgba(255,255,255,0) 100%),
      radial-gradient(ellipse 14% 30% at 30% 72%, var(--map-tint) 0%, rgba(255,255,255,0) 100%),
      radial-gradient(ellipse 34% 28% at 68% 28%, var(--map-tint) 0%, rgba(255,255,255,0) 100%),
      radial-gradient(ellipse 14% 24% at 52% 60%, var(--map-tint) 0%, rgba(255,255,255,0) 100%),
      radial-gradient(ellipse 12% 12% at 84% 78%, var(--map-tint) 0%, rgba(255,255,255,0) 100%);
  }
  .brand {
    position: absolute;
    left: 0; right: 0;
    top: 118px;
    display: flex;
    flex-direction: column;
    align-items: center;
    gap: 14px;
  }
  .brand-mark {
    width: 46px;
    height: 46px;
    border-radius: 50%;
    background: var(--white);
  }
  .brand-name {
    font-family: "Montserrat", sans-serif;
    font-weight: 500;
    font-size: 30px;
    letter-spacing: 3px;
    color: var(--white);
  }
  .front-web {
    position: absolute;
    left: 0; right: 0;
    top: 292px;
    text-align: center;
    font-family: "Didact Gothic", sans-serif;
    font-size: 18px;
    color: var(--white);
  }

  /* Back */
  .card-back {
    left: 80px;
    top: 480px;
    background: linear-gradient(120deg, var(--black) 0%, var(--black-soft) 45%, var(--black) 100%);
  }
  .identity {
    position: absolute;
    right: 360px;
    top: 140px;
    text-align: right;
  }
  .person-name {
    font-family: "Oswald", sans-serif;
    font-weight: 500;
    font-size: 32px;
    letter-spacing: 1px;
    color: var(--grey-text);
    line-height: 1;
  }
  .person-title {
    margin-top: 4px;
    font-size: 19px;
    color: var(--red);
  }
  .divider {
    position: absolute;
    left: 278px;
    top: 110px;
    width: 2px;
    height: 120px;
    background: var(--red);
  }
  .contacts {
    position: absolute;
    left: 296px;
    top: 106px;
    font-size: 17px;
    line-height: 22px;
    color: var(--contact-text);
    list-style: none;
  }
  .contacts .label { color: var(--red); }
  .contacts .with-icon { display: flex; align-items: center; gap: 6px; }
  .contacts svg { width: 14px; height: 14px; flex: none; }
  .contacts em { font-style: normal; color: var(--red); }
</style>
</head>
<body>
  <section class="card card-front">
    <div class="world-map-area" role="img" aria-label="Faint world map spread across the card, showing the company builds stands worldwide"></div>
    <div class="brand">
      <div class="brand-mark"></div>
      <div class="brand-name">VELMORA BUILDWORKS</div>
    </div>
    <div class="front-web">www.velmora-buildworks.com</div>
  </section>

  <section class="card card-back">
    <div class="identity">
      <div class="person-name">ADRIAN KELL</div>
      <div class="person-title">President</div>
    </div>
    <div class="divider"></div>
    <ul class="contacts">
      <li class="label">Singapore Contact:</li>
      <li>+65 81427730</li>
      <li class="label">Qatar Contact:</li>
      <li>+974 55208146</li>
      <li class="with-icon">
        <svg viewBox="0 0 14 14" aria-hidden="true"><rect x="1" y="3" width="12" height="9" rx="1" fill="#d0202a"/><path d="M1.5 3.5 7 8l5.5-4.5" stroke="#0c0c0d" stroke-width="1.2" fill="none"/></svg>
        info@velmora-buildworks.com
      </li>
      <li class="with-icon">
        <svg viewBox="0 0 14 14" aria-hidden="true"><circle cx="7" cy="7" r="6" fill="none" stroke="#d0202a" stroke-width="1.4"/><ellipse cx="7" cy="7" rx="2.6" ry="6" fill="none" stroke="#d0202a" stroke-width="1.1"/><path d="M1 7h12" stroke="#d0202a" stroke-width="1.1"/></svg>
        <span>www.<em>velmora-buildworks</em>.com</span>
      </li>
    </ul>
  </section>
</body>
</html>
```